Exciting & Elegant Stationary Pack

Stationary consists of
1. Letter head / Envelope
2. Business Card
3. Invoice
4. 40x40mm sticker

Attached files;

1. Logo (Other formats available on request)
2. MS word Doc - For information and description of design
3. Website image (This will be our new website so use the colours so everything ties together)
4. Sample of stationary pack we like, but feel free to be creative

Target Market(s)

Home improvement

Industry/Entity Type

Construction

Font styles to use
Other font styles liked:
• Leave up to designer - We like font used on (website attached image)

Requirements
Must have
• Please look at uploaded file of sample website and use colours
Nice to have
• Any type of business card design - eg. metal, die cut, embossed, etc...

```html
<!DOCTYPE html>
<html lang="en">
<head>
<meta charset="utf-8">
<title>Setline Tiling – Business Card</title>
<link href="https://fonts.googleapis.com/css2?family=Open+Sans:wght@400;600;800&display=swap" rel="stylesheet">
<style>
  :root {
    --navy: #0f4a6f;
    --navy-deep: #0b3a58;
    --orange: #f0913a;
    --white: #ffffff;
    --stage: #e9ecef;
    --shadow: rgba(0, 0, 0, 0.18);
  }
  * { box-sizing: border-box; margin: 0; padding: 0; }
  html, body {
    width: 1200px; height: 950px; overflow: hidden;
    background: var(--stage);
    font-family: "Open Sans", Arial, sans-serif;
  }
  .canvas { position: relative; width: 1200px; height: 950px; }
  .card {
    position: absolute; width: 640px; height: 391px; overflow: hidden;
    box-shadow: 0 10px 28px var(--shadow);
  }
  .card svg.shapes { position: absolute; inset: 0; width: 100%; height: 100%; }
  .card-front { left: 60px; top: 70px; background: var(--white); }
  .card-back { left: 500px; top: 500px; background: var(--navy); }

  .brand {
    position: absolute; color: var(--white);
    font-weight: 800; text-transform: uppercase; letter-spacing: 1px;
    white-space: nowrap;
  }
  .card-front .brand { left: 330px; width: 270px; top: 82px; text-align: center; font-size: 34px; }
  .card-back .brand { left: 170px; top: 120px; font-size: 40px; }

  .contact {
    position: absolute; left: 48px; top: 268px; color: var(--white);
    font-size: 15px; line-height: 1.5;
  }
  .contact .name { color: var(--orange); font-weight: 800; font-size: 21px; line-height: 1.3; }
  .contact .role, .contact .licence { font-weight: 400; }
  .contact ul { list-style: none; margin-top: 4px; }
  .contact li { display: flex; align-items: center; gap: 9px; }
  .contact li svg { width: 13px; height: 13px; flex: none; }
</style>
</head>
<body>
<main class="canvas">

  <section class="card card-front" aria-label="Business card front">
    <svg class="shapes" viewBox="0 0 640 391" aria-hidden="true">
      <polygon class="brand-plate" points="330,25 600,25 632,105 600,185 330,185 298,105" fill="var(--navy)"/>
      <polygon class="contact-plate-edge" points="0,391 0,290 38,234 400,234 452,312 452,391" fill="var(--orange)"/>
      <polygon class="contact-plate" points="0,391 0,294 43,242 395,242 443,314 443,391" fill="var(--navy)"/>
    </svg>
    <div class="brand">Setline Tiling</div>

    <div class="contact">
      <p class="name">Daniel Kerr</p>
      <p class="role">Project Manager</p>
      <p class="licence">Lic. No. 204618c</p>
      <ul>
        <li>
          <svg viewBox="0 0 14 14" aria-hidden="true"><rect x="3" y="1" width="8" height="12" rx="1.5" fill="none" stroke="var(--white)" stroke-width="1.4"/><circle cx="7" cy="10.8" r="0.8" fill="var(--white)"/></svg>
          0400 123 789
        </li>
        <li>
          <svg viewBox="0 0 14 14" aria-hidden="true"><rect x="1" y="3" width="12" height="8" fill="var(--orange)"/><path d="M1 3 L7 8 L13 3" fill="none" stroke="var(--white)" stroke-width="1.2"/></svg>
          hello@setlinetiling.com.au
        </li>
        <li>
          <svg viewBox="0 0 14 14" aria-hidden="true"><circle cx="7" cy="7" r="6" fill="var(--orange)"/><path d="M1 7 H13 M7 1 C4 4 4 10 7 13 M7 1 C10 4 10 10 7 13" fill="none" stroke="var(--white)" stroke-width="1"/></svg>
          www.setlinetiling.com.au
        </li>
      </ul>
    </div>
  </section>

  <section class="card card-back" aria-label="Business card back">
    <svg class="shapes" viewBox="0 0 640 391" aria-hidden="true">
      <polygon class="diagonal-band" points="0,391 0,285 330,185 430,185 180,391" fill="var(--white)"/>
    </svg>
    <div class="brand">Setline Tiling</div>
  </section>

</main>
</body>
</html>
```